Dental Medical History Form - Content provided

Design a medical history form for a dental practice. Content is provided so all that is needed is the formatting to make it look great and easy to read.

"Patient Information" to include all information contained in top portion of the "Patient Medical History Form" docx file.

"Medical History" should follow the formatting and content of the "Exact Medical History" file as this is what the entry fields look like in our practice software and so we would like it to match.

1st page - Patient info, allergies, medications, antibiotics, joint replacement, pregnancy.

2nd page - Do you have, or have you had, any of the following? . . . . . . .
Updates

Target Market(s)

All ages but must be clear enough for elderly to read. Use as much space as possible to keep font size bigger yet keep to two pages

Industry/Entity Type

Dental

Font styles to use
Sans Serif

Requirements
Must have
• All content provided
• Our logo at the top (file provided)
• Century Gothic Font
• Limit to two pages

```html
<!DOCTYPE html>
<html lang="en">
<head>
<meta charset="utf-8">
<title>Harbourline Dental – Confidential Medical History</title>
<link href="https://fonts.googleapis.com/css2?family=Questrial&display=swap" rel="stylesheet">
<style>
  :root{
    --ink:#2e2e30;
    --muted:#8a8a8c;
    --field:#dedfe2;
    --box:#d4d5d8;
    --band:#e3e2dc;
    --paper:#ffffff;
    --stage:#f1f1f1;
  }
  *{box-sizing:border-box;margin:0;padding:0}
  html,body{width:1200px;height:1200px;overflow:hidden;background:var(--stage)}
  body{font-family:"Questrial","Century Gothic",sans-serif;color:var(--ink);position:relative}
  .page{position:absolute;top:190px;width:570px;height:806px;background:var(--paper);
        box-shadow:0 2px 10px rgba(0,0,0,.12);padding:22px 26px;font-size:10.5px}
  .page--info{left:20px}
  .page--history{left:610px}

  .brand{display:flex;align-items:center;gap:6px;height:44px}
  .brand__name{font-size:26px;color:#555558;letter-spacing:.5px;line-height:1}
  .brand__dot{width:9px;height:9px;border-radius:50%;background:var(--muted);margin-top:-14px}

  .title-band{background:var(--band);margin:0 -26px;height:44px;display:flex;align-items:center;
              padding-left:150px;font-size:19px;letter-spacing:.8px}
  .pattern{role:img}

  .field{display:flex;align-items:center;gap:6px;margin-bottom:5px;white-space:nowrap}
  .field__bar{flex:1;height:11px;background:var(--field)}
  .sub{display:flex;font-size:8px;color:#555;margin:-3px 0 5px 50px;gap:0}
  .sub span{flex:1}

  .info-grid{display:grid;grid-template-columns:1fr 1fr;gap:24px;margin-top:14px}
  .group-label{margin:8px 0 4px}
  .box{display:inline-block;width:9px;height:9px;background:var(--box);vertical-align:middle;margin:0 6px 0 3px}

  .q{font-weight:700;margin:16px 0 8px;font-size:11.5px}
  .checks{display:flex;flex-wrap:wrap;gap:8px 4px;line-height:1.4}
  .checks span{white-space:nowrap}

  .med-lines{display:grid;grid-template-columns:repeat(3,1fr);gap:7px 14px;margin-top:4px}
  .med-lines i{display:block;height:11px;background:var(--field)}

  .yn-table{margin-top:18px;width:100%;border-collapse:collapse}
  .yn-table td{padding:4px 0;vertical-align:middle}
  .yn-table .ans{white-space:nowrap;width:150px}
  .yn-table b{font-weight:700}

  .footer{position:absolute;left:26px;right:26px;bottom:22px;display:flex;gap:12px;color:var(--muted);font-size:10.5px}

  /* history page */
  .history-title{font-weight:700;font-size:13px;margin:4px 0 12px}
  .cols{display:grid;grid-template-columns:1fr 1fr;gap:22px}
  .list-head{font-weight:700;margin:6px 0 3px}
  .row{display:flex;justify-content:space-between;height:15.2px;align-items:center}
  .row .yn{white-space:nowrap}
  .sign{margin-top:10px}
  .thanks{position:absolute;left:26px;right:26px;bottom:74px;font-size:10px;line-height:1.4}
  .end-band{position:absolute;left:0;right:0;bottom:0;height:58px;background:var(--band);
            display:flex;align-items:center;justify-content:flex-end;padding-right:26px}
  .end-band .brand{background:var(--paper);padding:6px 12px;height:40px}
  .end-band .brand__name{font-size:20px}
</style>
</head>
<body>

<section class="page page--info">
  <header class="brand">
    <span class="brand__name">harbourline dental</span><span class="brand__dot"></span>
  </header>
  <div class="title-band" role="img" aria-label="Title band with light woven chevron pattern">CONFIDENTIAL MEDICAL HISTORY</div>

  <div class="info-grid">
    <div class="patient">
      <div class="field">Name: <span class="field__bar"></span></div>
      <div class="sub"><span>Title</span><span>First</span><span>Middle</span><span>Last</span></div>
      <div class="field">Address: <span class="field__bar"></span></div>
      <div class="field">DOB: <span class="field__bar"></span></div>
      <div class="field">Email Address: <span class="field__bar"></span></div>
      <div class="field">Phone Number(s): <span class="field__bar"></span></div>
      <div class="sub" style="margin-left:100px"><span>Mobile</span><span>Work</span><span>Home</span></div>
      <div class="group-label">Emergency Contact Person:</div>
      <div class="field">Name: <span class="field__bar"></span></div>
      <div class="field">Relationship: <span class="field__bar"></span></div>
      <div class="field">Phone number: <span class="field__bar"></span></div>
    </div>
    <div class="practitioner">
      <div class="field">General Practitioner: <span class="field__bar"></span></div>
      <div class="field">Name: <span class="field__bar"></span></div>
      <div class="field">Practice Name: <span class="field__bar"></span></div>
      <div class="field">Phone Number: <span class="field__bar"></span></div>
      <div class="group-label" style="margin-top:12px">Do you have a health fund with dental cover?</div>
      <div class="field">Yes<span class="box"></span> or No<span class="box"></span> <span class="field__bar"></span></div>
      <div class="field">If so, what is the name of the fund? <span class="field__bar"></span></div>
      <div class="field">Fund Number? <span class="field__bar"></span></div>
      <div class="field">Priority Number on card: 0 1 2 3 4 5 <span class="field__bar"></span></div>
      <div class="field">Occupation: <span class="field__bar"></span></div>
      <div class="field">Referred by: <span class="field__bar"></span></div>
    </div>
  </div>

  <p class="q">Please indicate if you are allergic to any of the following ✓?</p>
  <div class="checks">
    <span>Aspirin<i class="box"></i></span><span>Codeine<i class="box"></i></span><span>Penicillin<i class="box"></i></span>
    <span>Sulfites<i class="box"></i></span><span>Latex<i class="box"></i></span><span>Local Anaesthetic<i class="box"></i></span>
    <span>Lactose<i class="box"></i></span><span>Nickel<i class="box"></i></span>
  </div>
  <div class="field" style="margin-top:8px">Other <span class="field__bar"></span></div>

  <p class="q">Are you currently taking, or have ever taken, any of the following medication ✓?</p>
  <div class="checks">
    <span>Asthma inhaler<i class="box"></i></span><span>Anti-epileptics<i class="box"></i></span><span>Anti-depressants<i class="box"></i></span>
    <span>Blood Pressure<i class="box"></i></span><span>Blood Thinners<i class="box"></i></span><span>Bisphosphonates<i class="box"></i></span>
    <span>Chemotherapy<i class="box"></i></span><span>Insulin<i class="box"></i></span><span>Immunosuppressants<i class="box"></i></span>
    <span>Steroids<i class="box"></i></span><span>Oral Contraceptive<i class="box"></i></span><span>Other<i class="box"></i></span>
  </div>

  <p class="q">Please specify medication name, dose, and frequency where possible:</p>
  <div class="med-lines">
    <i></i><i></i><i></i><i></i><i></i><i></i><i></i><i></i><i></i><i></i><i></i><i></i>
  </div>

  <table class="yn-table">
    <tr><td><b>Do you require antibiotic cover?</b></td><td class="ans">Yes<i class="box"></i> No<i class="box"></i></td></tr>
    <tr><td><b>Have you had a joint replacement?</b></td><td class="ans">Yes<i class="box"></i> No<i class="box"></i></td></tr>
    <tr><td style="padding-top:12px">Women:<br><b>Are you pregnant?</b></td><td class="ans" style="padding-top:12px">Yes<i class="box"></i> No<i class="box"></i> Possible<i class="box"></i></td></tr>
    <tr><td>or &nbsp;<b>Breast Feeding?</b></td><td class="ans">Yes<i class="box"></i> No<i class="box"></i></td></tr>
  </table>

  <footer class="footer">
    <span>Harbourline Dental</span><span>|</span><span>Suite 4, 18 Marlow Street</span><span>|</span><span>Keelby NSW 2260</span><span>|</span><span>(02) 4000 1234</span>
  </footer>
</section>

<section class="page page--history">
  <h2 class="history-title">Do you have, or have you had, any of the following?</h2>
  <div class="cols">
    <div>
      <p class="list-head">Dental</p>
      <div class="row"><span>Acid Reflux</span><span class="yn">Yes<i class="box"></i>No<i class="box"></i></span></div>
      <div class="row"><span>Bad Breath/Taste</span><span class="yn">Yes<i class="box"></i>No<i class="box"></i></span></div>
      <div class="row"><span>Bleeding/Swollen/Sore Gums</span><span class="yn">Yes<i class="box"></i>No<i class="box"></i></span></div>
      <div class="row"><span>Blisters/Ulcers in Mouth</span><span class="yn">Yes<i class="box"></i>No<i class="box"></i></span></div>
      <div class="row"><span>Broken tooth/filling</span><span class="yn">Yes<i class="box"></i>No<i class="box"></i></span></div>
      <div class="row"><span>Burning tongue</span><span class="yn">Yes<i class="box"></i>No<i class="box"></i></span></div>
      <div class="row"><span>Dry mouth</span><span class="yn">Yes<i class="box"></i>No<i class="box"></i></span></div>
      <div class="row"><span>Food collection between teeth</span><span class="yn">Yes<i class="box"></i>No<i class="box"></i></span></div>
      <div class="row"><span>Grinding/clenching teeth (day/night)</span><span class="yn">Yes<i class="box"></i>No<i class="box"></i></span></div>
      <div class="row"><span>Jaw pain</span><span class="yn">Yes<i class="box"></i>No<i class="box"></i></span></div>
      <div class="row"><span>Loose teeth</span><span class="yn">Yes<i class="box"></i>No<i class="box"></i></span></div>
      <div class="row"><span>Toothache</span><span class="yn">Yes<i class="box"></i>No<i class="box"></i></span></div>
      <div class="row"><span>Sensitive to hot/cold</span><span class="yn">Yes<i class="box"></i>No<i class="box"></i></span></div>
      <div class="row"><span>Difficulty chewing</span><span class="yn">Yes<i class="box"></i>No<i class="box"></i></span></div>
      <div class="row"><span>Difficulty swallowing</span><span class="yn">Yes<i class="box"></i>No<i class="box"></i></span></div>
      <div class="row"><span>Orthodontic history</span><span class="yn">Yes<i class="box"></i>No<i class="box"></i></span></div>

      <p class="list-head" style="margin-top:12px">Blood</p>
      <div class="row"><span>Bleeding tendency</span><span class="yn">Yes<i class="box"></i>No<i class="box"></i></span></div>
      <div class="row"><span>Anaemia</span><span class="yn">Yes<i class="box"></i>No<i class="box"></i></span></div>
      <div class="row"><span>Blood disorders</span><span class="yn">Yes<i class="box"></i>No<i class="box"></i></span></div>
      <div class="row"><span>Lung disease</span><span class="yn">Yes<i class="box"></i>No<i class="box"></i></span></div>

      <p class="list-head" style="margin-top:12px">Lifestyle</p>
      <div class="row"><span>Smoking</span><span class="yn">Yes<i class="box"></i>No<i class="box"></i></span></div>
      <div class="row"><span>Alcohol</span><span class="yn">Yes<i class="box"></i>No<i class="box"></i></span></div>
      <div class="row"><span>Vaping</span><span class="yn">Yes<i class="box"></i>No<i class="box"></i></span></div>

      <div class="sign">
        <div class="field">Signature: <span class="field__bar"></span></div>
        <div class="field">Date: <span class="field__bar"></span></div>
      </div>
    </div>

    <div>
      <p class="list-head">Heart</p>
      <div class="row"><span>Angina</span><span class="yn">Yes<i class="box"></i>No<i class="box"></i></span></div>
      <div class="row"><span>Atrial Fibrillation</span><span class="yn">Yes<i class="box"></i>No<i class="box"></i></span></div>
      <div class="row"><span>Blood Pressure (High/Low)</span><span class="yn">Yes<i class="box"></i>No<i class="box"></i></span></div>
      <div class="row"><span>Congenital Heart Disease</span><span class="yn">Yes<i class="box"></i>No<i class="box"></i></span></div>
      <div class="row"><span>Heart attack</span><span class="yn">Yes<i class="box"></i>No<i class="box"></i></span></div>
      <div class="row"><span>Heart murmur</span><span class="yn">Yes<i class="box"></i>No<i class="box"></i></span></div>
      <div class="row"><span>Heart surgery</span><span class="yn">Yes<i class="box"></i>No<i class="box"></i></span></div>
      <div class="row"><span>Heart valve replacement</span><span class="yn">Yes<i class="box"></i>No<i class="box"></i></span></div>
      <div class="row"><span>Infective endocarditis</span><span class="yn">Yes<i class="box"></i>No<i class="box"></i></span></div>
      <div class="row"><span>Rheumatic Heart Disease</span><span class="yn">Yes<i class="box"></i>No<i class="box"></i></span></div>
      <div class="row"><span>Pacemaker</span><span class="yn">Yes<i class="box"></i>No<i class="box"></i></span></div>
      <div class="row"><span>Stent</span><span class="yn">Yes<i class="box"></i>No<i class="box"></i></span></div>

      <p class="list-head" style="margin-top:12px">Other</p>
      <div class="row"><span>Anxiety/PTSD</span><span class="yn">Yes<i class="box"></i>No<i class="box"></i></span></div>
      <div class="row"><span>Arthritis</span><span class="yn">Yes<i class="box"></i>No<i class="box"></i></span></div>
      <div class="row"><span>Alzheimer's</span><span class="yn">Yes<i class="box"></i>No<i class="box"></i></span></div>
      <div class="row"><span>Asthma</span><span class="yn">Yes<i class="box"></i>No<i class="box"></i></span></div>
      <div class="row"><span>Anaphylaxis</span><span class="yn">Yes<i class="box"></i>No<i class="box"></i></span></div>
      <div class="row"><span>Auto-immune disease</span><span class="yn">Yes<i class="box"></i>No<i class="box"></i></span></div>
      <div class="row"><span>Coeliac</span><span class="yn">Yes<i class="box"></i>No<i class="box"></i></span></div>
      <div class="row"><span>Depression</span><span class="yn">Yes<i class="box"></i>No<i class="box"></i></span></div>
      <div class="row"><span>Diabetes</span><span class="yn">Yes<i class="box"></i>No<i class="box"></i></span></div>
      <div class="row"><span>Epilepsy</span><span class="yn">Yes<i class="box"></i>No<i class="box"></i></span></div>
      <div class="row"><span>Kidney Disease</span><span class="yn">Yes<i class="box"></i>No<i class="box"></i></span></div>
      <div class="row"><span>Liver Disease</span><span class="yn">Yes<i class="box"></i>No<i class="box"></i></span></div>
      <div class="row"><span>Osteoporosis</span><span class="yn">Yes<i class="box"></i>No<i class="box"></i></span></div>
      <div class="row"><span>Parkinson's</span><span class="yn">Yes<i class="box"></i>No<i class="box"></i></span></div>
      <div class="row"><span>Radiation to Head/Neck</span><span class="yn">Yes<i class="box"></i>No<i class="box"></i></span></div>
      <div class="row"><span>Schizophrenia</span><span class="yn">Yes<i class="box"></i>No<i class="box"></i></span></div>
      <div class="row"><span>Snoring</span><span class="yn">Yes<i class="box"></i>No<i class="box"></i></span></div>
      <div class="row"><span>Sleep apnea</span><span class="yn">Yes<i class="box"></i>No<i class="box"></i></span></div>
      <div class="row"><span>Stroke</span><span class="yn">Yes<i class="box"></i>No<i class="box"></i></span></div>
      <div class="field" style="margin-top:6px">Other: <span class="field__bar"></span></div>
    </div>
  </div>

  <p class="thanks">Thank you for the time to complete your medical history form. Oral health is linked to overall health and this comprehensive questionnaire will help us to provide you with optimal and safe care.</p>
  <div class="end-band" role="img" aria-label="Closing band with light woven chevron pattern">
    <div class="brand"><span class="brand__name">harbourline dental</span><span class="brand__dot"></span></div>
  </div>
</section>

</body>
</html>
```